Design Startseite Kanzlei-Homepage
Zielgruppe
Wir sind eine Rechtsanwaltskanzlei in Kempten (Allgäu) und regional sowie überregional in verschiedenen Rechtsgebieten tätig. Unsere Zielgruppe sind sowohl private als auch gewerbliche Mandanten.
Aufgabenstellung
Die bestehende Gestaltung wirkt derzeit aus unserer Sicht überholt. Insbesondere soll das bislang dominierende Rot vollständig entfallen.
Stattdessen stellen wir uns ein modernes, hochwertiges Erscheinungsbild vor, primär in dunklen Farbtönen (Anthrazit/Schwarz) kombiniert mit Beige- bzw. warmen Naturtönen. Ziel ist eine klare visuelle Anlehnung an unsere Kanzleiräumlichkeiten (siehe Fotos).
Die Webseite soll insgesamt moderner, klarer und visuell anspruchsvoller wirken, ohne an Seriosität und Zugänglichkeit einzubüßen. Die Balance zwischen hochwertigem Erscheinungsbild und mandantenorientierter Nutzerführung steht für uns im Vordergrund.

```html
<!DOCTYPE html>
<html lang="de">
<head>
<meta charset="utf-8">
<title>Kanzlei am Ringplatz – Startseite</title>
<link href="https://fonts.googleapis.com/css2?family=Cinzel:wght@400;500&family=Fira+Sans:wght@400;500;600&family=Fira+Sans+Condensed:wght@500;600&display=swap" rel="stylesheet">
<style>
  :root {
    --bronze: #8b6b4e;
    --bronze-dark: #7a5c42;
    --anthracite: #2c2c2c;
    --ink: #222222;
    --white: #ffffff;
    --hero-overlay: rgba(35, 33, 31, 0.78);
  }
  * { margin: 0; padding: 0; box-sizing: border-box; }
  html, body { width: 1193px; height: 1200px; overflow: hidden; background: var(--white); }
  body { position: relative; font-family: "Fira Sans", Arial, sans-serif; color: var(--ink); }

  .topbar {
    position: absolute; left: 0; top: 0; width: 1193px; height: 17px;
    background: var(--bronze); color: var(--white);
    font-size: 7px; display: flex; align-items: center; gap: 20px; padding-left: 215px;
  }
  .topbar span { display: flex; align-items: center; gap: 5px; }

  .navbar {
    position: absolute; left: 0; top: 17px; width: 1193px; height: 50px;
    background: var(--anthracite);
  }
  .brand {
    position: absolute; left: 213px; top: 13px;
    font-family: "Fira Sans Condensed", Arial, sans-serif; font-weight: 600;
    font-size: 22px; letter-spacing: 0.5px; color: var(--white);
  }
  .nav { position: absolute; left: 550px; top: 0; height: 50px; display: flex; list-style: none; }
  .nav li {
    height: 50px; display: flex; align-items: center; padding: 0 14px;
    color: var(--white); font-size: 13px; font-weight: 500;
  }
  .nav li.active { background: var(--bronze); padding: 0 15px; }

  .photo { position: absolute; }
  .photo-hero {
    left: 0; top: 67px; width: 1193px; height: 431px;
    background: linear-gradient(100deg, #8a6b4e 0%, #a58565 25%, #5b5650 45%, #c9c6c0 62%, #3b3a39 78%, #7b7671 100%);
  }
  .photo-team {
    left: 567px; top: 449px; width: 626px; height: 375px;
    background: linear-gradient(180deg, #9d9b98 0%, #7c7a77 45%, #3a3a3c 70%, #a9a7a4 100%);
  }
  .photo-meeting {
    left: 0; top: 824px; width: 567px; height: 376px;
    background: linear-gradient(120deg, #f1f1ef 0%, #d8d4cc 35%, #34404a 60%, #e8e6e2 100%);
  }

  .hero-title {
    position: absolute; left: 109px; top: 306px; width: 430px; height: 67px;
    background: var(--hero-overlay); color: var(--white);
    font-family: "Cinzel", Georgia, serif; font-size: 21px; line-height: 25px;
    padding: 9px 10px;
  }

  .icon-tile {
    position: absolute; width: 56px; height: 56px; background: var(--bronze);
    display: flex; align-items: center; justify-content: center;
  }
  .icon-tile.one { left: 511px; top: 500px; }
  .icon-tile.two { left: 567px; top: 824px; }

  .intro { position: absolute; }
  .intro.team { left: 105px; top: 542px; width: 320px; }
  .intro.second { left: 699px; top: 921px; width: 320px; }
  .eyebrow {
    font-family: "Cinzel", Georgia, serif; font-size: 10px; color: var(--bronze);
    letter-spacing: 0.3px; margin-bottom: 9px;
  }
  .section-title {
    font-family: "Cinzel", Georgia, serif; font-weight: 400; font-size: 17.5px; line-height: 21px;
    color: var(--bronze-dark); border-left: 2px solid var(--bronze); padding-left: 10px; margin-bottom: 13px;
  }
  .body-copy { font-size: 7.7px; line-height: 11.2px; color: var(--ink); }
  .body-copy p + p { margin-top: 11px; }
  .button {
    display: inline-block; margin-top: 16px; background: var(--bronze); color: var(--white);
    font-size: 8.5px; font-weight: 600; padding: 4px 9px;
  }
</style>
</head>
<body>
  <div class="topbar">
    <span>
      <svg width="9" height="7" viewBox="0 0 9 7"><rect x="0.5" y="0.5" width="8" height="6" fill="none" stroke="#fff"/><path d="M0.5 0.5 L4.5 4 L8.5 0.5" fill="none" stroke="#fff"/></svg>
      info@kanzleiamringplatz.de
    </span>
    <span>
      <svg width="8" height="8" viewBox="0 0 8 8"><path d="M1.5 0.5 L3 2.3 L2.2 3.2 Q3.3 5 4.8 5.8 L5.7 5 L7.5 6.5 L6.6 7.5 Q2.5 7 0.5 1.4 Z" fill="#fff"/></svg>
      0831 555 014 7
    </span>
  </div>

  <header class="navbar">
    <div class="brand">KANZLEI AM RINGPLATZ</div>
    <ul class="nav">
      <li class="active">Startseite</li>
      <li>Rechtsgebiete</li>
      <li>Kanzlei</li>
      <li>Kontakt</li>
    </ul>
  </header>

  <div class="photo photo-hero" role="img" aria-label="Empfangsbereich der Kanzlei mit Holzverkleidung, hellem Tresen und Deckenleuchten"></div>
  <h1 class="hero-title">Rechtsanwälte und Fachanwälte<br>in Kempten: Kanzlei am Ringplatz</h1>

  <div class="photo photo-team" role="img" aria-label="Gruppenfoto des Kanzleiteams auf einem gepflasterten Platz"></div>

  <div class="icon-tile one">
    <svg width="28" height="26" viewBox="0 0 28 26" fill="none" stroke="#fff" stroke-width="1.4">
      <path d="M2 8 L14 2 L26 8 Z"/>
      <line x1="3" y1="10" x2="25" y2="10"/>
      <line x1="6" y1="12" x2="6" y2="20"/><line x1="11" y1="12" x2="11" y2="20"/>
      <line x1="17" y1="12" x2="17" y2="20"/><line x1="22" y1="12" x2="22" y2="20"/>
      <line x1="3" y1="22" x2="25" y2="22"/><line x1="1" y1="24.5" x2="27" y2="24.5"/>
    </svg>
  </div>

  <section class="intro team">
    <div class="eyebrow">UNSER ANWALTSTEAM</div>
    <h2 class="section-title">Rechtsanwälte und Fachanwälte<br>in Kempten: Kanzlei am Ringplatz</h2>
    <div class="body-copy">
      <p>Die Mitglieder unseres Anwaltsteams – jeweils ergänzt um ein ansprechend eingerichtetes und funktional ausgestattetes Sekretariat – spezialisieren sich in unterschiedliche Fachrichtungen, sodass für Sie eine große Bandbreite in der mandantenorientierten Rechtsberatung sichergestellt ist. Das gilt insbesondere für unsere Schwerpunkte im Verkehrsrecht und Strafrecht sowie im Arbeitsrecht, Erbrecht, Mietrecht, Baurecht und Familienrecht.</p>
      <p>Auf die Mandatierung externer Anwälte kann durch die thematische Vielfalt und Spezialisierung unserer Juristen in den meisten Fällen verzichtet werden. Gleichzeitig gewährleistet unser engagiertes Kanzleiteam eine rechtliche Unterstützung ganz nach Ihren individuellen Interessen, stets auf dem neuesten Stand von Rechtsprechung und Praxis.</p>
    </div>
    <span class="button">Infos und Terminvereinbarung</span>
  </section>

  <div class="photo photo-meeting" role="img" aria-label="Besprechung von drei Anwälten an einem hellen Tisch"></div>

  <div class="icon-tile two">
    <svg width="26" height="26" viewBox="0 0 26 26" fill="none" stroke="#fff" stroke-width="1.4">
      <path d="M4 22 L22 4"/><path d="M15 4 L22 4 L22 11"/><path d="M4 15 Q10 10 11 4"/><path d="M22 15 Q16 16 11 22"/>
    </svg>
  </div>

  <section class="intro second">
    <div class="eyebrow">LOREM IPSUM</div>
    <h2 class="section-title">Nulpa quunt parcidendion<br>rectus ut lat quodipis solesti</h2>
    <div class="body-copy">
      <p>Nost, quo vid quam eatur?<br>Nulpa quunt parcidendion rectus ut lat quodipis solesti derum sit endunt ditatur reped magnatum et ipicatur aborit eium abor aut molesto berum la pore, ut est occusanis alitaquas abo. Unt qui venti re vel milit imod quis ma volorunt ea alicae.</p>
      <p>Sit quodis dendebis moluptam quam nos quodis eum dolorpos quunt et hil ipsae niendi nonsed es ut quossitin pla necta consequi voluptaquat eturis assitia spedicit at aut doloris dia sandit que sin eos aligeni mporem faceper ehenden imenisitur? Lacerunt andisitio. Nam as quatur, iumque ne velessinctis dicitsti blaborum excepel id modit exera volupta volupta tiorem acculpa quam, iiitect ibusam, non rest offic to bea eum nihil exerfer speres mod eossum quiasped.</p>
    </div>
    <span class="button">Lorem Ipsum</span>
  </section>
</body>
</html>
```